Recto Verso Audiology Business Card

Business card with a beautiful design on the back. On the Recto you need the following data Lindqvist Oren Audiologist Hearing Solutions Hearing Protection Tinnitus Hyperacusis Tel: 0482/37 59 08 Email: On the back, you need something nice like the attached file. The logo "Corra Luna" can be in the center The colors of the Logo can not be changed If possible stay in the same colors as the logo Another solution is to put the logo on the front and have a nice back (A mosaic of small ears, hearing aids or other ..) Thank you _______________________________________________________________ Visit card On the Recto Lindqvist Oren Audiologist Hearing Solutions Hearing Protection Tinnitus Hyperacusis Tel: 0482/37 59 08 Email: You can put the logo " Corra Luna "on the Recto of the Verso The colors of the logo can not be changed. If you put the logo on the back, it must be well integrated. On the Verso I need something in the files. something stylish. It's a visit card for an audiologist. You can get ears of hearing aids if you need. Thanks

Target Market(s)

customers

Contact Information for Business Card

Carte de visite standard ou A6

Font styles to use
Serif
Sans Serif

Colors
33a6d7

Requirements
Must have
• the logo and a stylized background.
Nice to have
• It would be nice to have a back side related to audiology (ears, hearing aids etc.)

```html
<!DOCTYPE html>
<html lang="en">
<head>
<meta charset="UTF-8">
<title>Corra Luna Audiology Business Card</title>
<link rel="stylesheet" href="https://fonts.googleapis.com/css2?family=Barlow:wght@400;500&display=swap">
<style>
  :root {
    --backdrop: #e6ddd3;
    --paper: #f7f6f2;
    --gold-light: #f3e6a6;
    --gold: #d9b83a;
    --gold-deep: #c49f1f;
    --teal: #3a9aa8;
    --ink: #3d3f42;
    --ink-soft: #55585c;
  }
  * { box-sizing: border-box; margin: 0; padding: 0; }
  html, body {
    width: 1200px;
    height: 870px;
    overflow: hidden;
    background: var(--backdrop);
    font-family: "Barlow", Arial, sans-serif;
  }
  .stage {
    position: relative;
    width: 1200px;
    height: 870px;
  }
  .card {
    position: absolute;
    width: 620px;
    height: 400px;
    background: var(--paper);
    box-shadow: 0 4px 14px rgba(80, 60, 40, 0.18);
    overflow: hidden;
  }
  .card--front { left: 110px; top: 40px; }
  .card--back { left: 470px; top: 440px; }

  .ear-pattern {
    position: absolute;
    inset: 0;
    background:
      radial-gradient(circle at 50% 50%, var(--paper) 0 18%, transparent 60%),
      linear-gradient(135deg, var(--gold-light), var(--gold) 45%, var(--gold-light) 70%, var(--gold-deep));
    opacity: 0.85;
  }
  .brand {
    position: absolute;
    left: 50%;
    top: 50%;
    transform: translate(-50%, -50%);
    width: 190px;
    padding: 18px 14px;
    background: var(--paper);
    display: flex;
    align-items: flex-start;
    gap: 10px;
  }
  .brand__mark {
    flex: none;
    width: 10px;
    height: 10px;
    margin-top: 8px;
    background: var(--gold);
  }
  .brand__name {
    color: var(--gold);
    font-weight: 400;
    font-size: 26px;
    line-height: 1.05;
    letter-spacing: 1.5px;
    text-transform: uppercase;
  }

  .contact {
    position: absolute;
    left: 60px;
    top: 128px;
    color: var(--ink-soft);
  }
  .contact__name {
    color: var(--teal);
    font-weight: 500;
    font-size: 24px;
    letter-spacing: 1px;
    text-transform: uppercase;
    line-height: 1;
  }
  .contact__role {
    color: var(--ink);
    font-size: 17px;
    letter-spacing: 1px;
    text-transform: uppercase;
    margin-top: 4px;
  }
  .contact__lines {
    list-style: none;
    margin-top: 12px;
    font-size: 16px;
    line-height: 1.2;
  }
  .contact__lines .phone { font-size: 18px; letter-spacing: 0.5px; }
  .services {
    margin-top: 12px;
    font-size: 16px;
    line-height: 1.2;
  }
  .services .dot {
    display: inline-block;
    width: 6px;
    height: 6px;
    border-radius: 50%;
    background: var(--teal);
    vertical-align: middle;
    margin: 0 4px;
  }
</style>
</head>
<body>
<main class="stage">
  <section class="card card--front" aria-label="Card front">
    <div class="ear-pattern" role="img" aria-label="Gold foil pattern of small ears with sound waves"></div>
    <div class="brand">
      <span class="brand__mark"></span>
      <span class="brand__name">Medical Center Corra Luna</span>
    </div>
  </section>

  <section class="card card--back" aria-label="Card back">
    <div class="contact">
      <h1 class="contact__name">Lindqvist Oren</h1>
      <p class="contact__role">Audiologist Hearing</p>
      <ul class="contact__lines">
        <li class="phone">0482/37 59 08</li>
        <li>info@medicalcentercorraluna.com</li>
        <li>medicalcentercorraluna.com</li>
      </ul>
      <p class="services">
        Solutions Hearing<br>
        Protection<span class="dot"></span>Tinnitus<br>
        Hyperacusis
      </p>
    </div>
  </section>
</main>
</body>
</html>
```